Coffee and Plastics

I am looking for a completely new site that shows the products we have. Our current site is www.velmorebrothersbeans.com. We are open minded to what designers come up with. Our current site is www.velmorebrothersbeans.com. You can you the information from there to start the site. I need these tabs on the main home page. ( Home, Coffee & Tea, Condiments, and Paper and Plastics, and Contact.) You can take photos and info from my Current site. In products page.
I will be uploading info and photo for paper and plastics.
Look and feel
Each slider illustrates characteristics of the customer's brand and the style your logo design should communicate.

```html
<!DOCTYPE html>
<html lang="en">
<head>
<meta charset="utf-8">
<title>Velmore Brothers Beans</title>
<link href="https://fonts.googleapis.com/css2?family=Lato:wght@300;900&family=Open+Sans:wght@400&family=Arimo:ital,wght@0,400;0,700;1,400&display=swap" rel="stylesheet">
<style>
:root{
  --roast:#5e1f10;
  --logo:#6b2414;
  --heading:#7a2a18;
  --nav:#f5a300;
  --nav-active:#e8541c;
  --accent:#d2451e;
  --paper:#ffffff;
  --ink:#4a2418;
}
*{margin:0;padding:0;box-sizing:border-box}
html,body{width:1200px;height:1012px;overflow:hidden;background:var(--paper)}
.page{position:relative;width:1200px;height:1012px;overflow:hidden}
.hero-photo{position:absolute;left:0;top:0;width:1200px;height:528px;
  background:linear-gradient(90deg,#ffffff 0%,#fbf8f6 25%,#e9dfd8 45%,#8a5a42 70%,#5a2e1c 100%)}
.brand{position:absolute;left:41px;top:34px;font-family:"Lato",sans-serif;font-weight:900;
  font-size:54px;letter-spacing:-0.5px;color:var(--logo);line-height:1}
.hours{position:absolute;left:41px;top:97px;font-family:"Arimo",sans-serif;font-size:15px;color:var(--ink)}
.hours .phone{font-weight:700;margin-right:22px}
.hours span+span{margin-right:30px}
.main-nav{position:absolute;left:390px;top:139px;display:flex;gap:30px;
  font-family:"Open Sans",sans-serif;font-size:21px;list-style:none}
.main-nav a{color:var(--nav);text-decoration:none}
.main-nav a.current{color:var(--nav-active)}
.welcome{position:absolute;left:50px;top:478px;font-family:"Lato",sans-serif;font-weight:300;
  font-size:38px;color:var(--heading)}
.intro{position:absolute;left:0;top:528px;width:1200px;height:484px;background:var(--roast);
  color:#fff;font-family:"Arimo",sans-serif}
.col{position:absolute;top:42px;font-size:15.5px;line-height:19.5px}
.col p+p{margin-top:19px}
.col-left{left:44px;width:540px}
.col-right{left:604px;width:510px}
.guarantee{position:absolute;left:48px;top:248px;font-style:italic;font-size:19px}
.serving{position:absolute;left:46px;top:351px;font-size:19.5px;color:var(--accent)}
.partners{position:absolute;left:0;top:397px;width:1200px;height:70px}
.badge{position:absolute}
</style>
</head>
<body>
<div class="page">
  <div class="hero-photo" role="img" aria-label="Roasted coffee beans scattered on a white surface"></div>
  <div class="brand">Velmore Brothers Beans</div>
  <div class="hours"><span class="phone">1-800-555-0142</span><span>MON - FRI</span><span>9 - 5 CENTRAL TIME</span></div>
  <ul class="main-nav">
    <li><a href="#">HOME</a></li>
    <li><a href="#">TEA &amp; COFFEE</a></li>
    <li><a href="#">CONDIMENTS</a></li>
    <li><a href="#" class="current">PAPER &amp; PLASTICS</a></li>
    <li><a href="#">CONTACT</a></li>
  </ul>
  <h1 class="welcome">Welcome to Velmore Brothers Beans !</h1>
  <section class="intro">
    <div class="col col-left">
      <p>We are a family-owned and operated business based in Alder Creek Texas. Since the opening of Velmore Brothers Beans plant in 1995, we have become Texas' premier independently owned coffee packaging company. Our success relies solely on the principle of selling only the freshest, highest-quality in-room coffee available.</p>
      <p>Velmore Brothers packages and supplies in-room coffee, tea products, and condiments. Whether we're supplying a 50-room Hotel or a 500-room grand resort,</p>
    </div>
    <div class="col col-right">
      <p>we have the distribution capacity to fill your rooms with the most aromatic and robust coffees and teas available at competitive prices.</p>
      <p>Velmore Brothers is continuously striving for ways to improve quality and product appearance to meet the highest standards in today's franchises and independent hotels. We are very aware that our success depends entirely upon maintaining our customers' confidence in our products, so we pay close attention to your needs every step of the way.</p>
    </div>
    <p class="guarantee">We guarantee all of our products will meet your level of satisfaction.</p>
    <p class="serving">SERVING FINE ESTABLISHMENTS EVERYWHERE !</p>
    <svg class="partners" width="1200" height="70" viewBox="0 0 1200 70" role="img" aria-label="Partner hotel badges">
      <rect x="46" y="0" width="90" height="45" fill="#3a6fd0"/>
      <rect x="157" y="2" width="106" height="42" fill="#ffffff"/>
      <rect x="289" y="0" width="84" height="55" rx="8" fill="#2b3a8c"/>
      <rect x="406" y="6" width="60" height="62" fill="#1f5aa8"/>
      <rect x="495" y="4" width="68" height="62" fill="#2a2f7a"/>
      <rect x="587" y="4" width="58" height="64" fill="#1f6e3c"/>
      <rect x="677" y="0" width="63" height="69" rx="4" fill="#a8152a"/>
      <rect x="772" y="0" width="90" height="45" fill="#3a6fd0"/>
      <rect x="884" y="2" width="106" height="42" fill="#ffffff"/>
      <rect x="1017" y="0" width="84" height="55" rx="8" fill="#2b3a8c"/>
    </svg>
  </section>
</div>
</body>
</html>
```